Marrowind - IT Consultancy Website

Our company is called Marrowind and our purpose is to help companies sustainably embrace and reap the benefits of cloud platforms, through transforming practices, skills and technology using DevOps and Security practices such that they are able to automate, manage and secure their cloud platforms to deliver product to market with increasing velocity.

To get our business started I require a website that will model the typical layout of an IT consultancy services company to an Australian Market. There are many examples of such a site, here are some of them. We would like a landing page and then a few simple menu options (About, Blog, Services etc..) to additional content

http://pelvo.com.au/
http://www.brisket.com.au/
http://www.tandu.com.au/

I require the site to be created with a separate CSS file that maintains the colour palette. This is a very important requirement, I want to be able to change the colours employed in the site in a single location and not have to scan through multiple files to replace the codes.

The website must be built using static content as it will not be hosted on a web server but instead in QNT using S3 and CloudFront CDN. Therefore please stick to HTML, JavaScript, CSS and other static file formats. The website needs to be response, smooth and reactive. It should render on desktop, mobile and tablet and feature smooth scrolling, transitions and fade in's.

The website should give the customer confidence that they are dealing with a highly professional IT services company, focused strongly on cloud (QNT, Vantrel Skyline, Horvik Vapor etc..), motivated by beautiful and fluid design.

In order to make this simpler for you, the designer, I have already purchased this template from https://skinmarketly.com/theme/the-venture-allround-template-KX7Q41093 and uploaded it. Feel free to use this template if you choose (note that it makes use of a separate color palette which is a key requirement) or use one of your own choosing. If you do use this template ensure that it does not look too much like "another bootstrap site" therefore use the layout and widgets but make the site look fresh and original too.
Obviously you must delete all trace of the bootstrap package once the project has completed if you do use it

Target Market(s)

Corporate and medium enterprise businesses

Industry/Entity Type

Information Technology

Coding

Coded - Design and coding required

Number of Pages Required

4 page

Font styles to use
Sans Serif

Colors
abd036
33a6d7

Requirements
Must have
• The website should give the customer confidence that they are dealing with a highly professional IT services company, focused strongly on cloud (QNT, Vantrel Skyline, Horvik Vapor etc..), motivated by beautiful and fluid design. Our company name is Marrowind, the site needs to pay homage to the themes of fluidity and logic
• Along with About Us, Services and a Blog page could I also get social logo's included too
Nice to have
• The website must be built using static content as it will not be hosted on a web server but instead in QNT using S3 and CloudFront CDN. Therefore please stick to HTML, JavaScript, CSS and other static file formats. The website needs to be response, smooth and reactive. It should render on desktop, mobile and tablet and feature smooth scrolling, transitions and fade in's.
Should not have
• Lurid colours, or too much animations. The design must "flow"

```html
<!DOCTYPE html>
<html lang="en">
<head>
<meta charset="utf-8">
<title>Marrowind IT Consultancy</title>
<link rel="stylesheet" href="https://fonts.googleapis.com/css2?family=Montserrat:wght@400;500;600&family=Open+Sans:ital,wght@0,400;0,600;1,400&display=swap">
<style>
:root{
  --blue:#2f8fd6;
  --blue-dark:#1a6fb8;
  --navy:#0f1d33;
  --ink:#222;
  --muted:#8a8a8a;
  --grey-bg:#f3f3f3;
  --line:#e2e2e2;
  --orange:#f7921c;
  --orange-dark:#f07a10;
  --white:#fff;
  --bar:#e4e4e4;
}
*{box-sizing:border-box;margin:0;padding:0}
html,body{width:1200px;height:2187px;overflow:hidden}
body{font-family:"Open Sans",Arial,sans-serif;color:var(--ink);background:var(--white);position:relative}
h1,h2,h3,h4,.brand,.nav a{font-family:"Montserrat",Arial,sans-serif;font-weight:400}
section,header,footer{position:absolute;left:0;width:1200px}

/* hero */
.hero{top:0;height:497px;overflow:hidden}
.hero-visual{position:absolute;inset:0;background:
  radial-gradient(circle at 60% 38%,rgba(214,90,220,.55) 0,rgba(90,80,200,.25) 12%,transparent 30%),
  radial-gradient(ellipse at 70% 60%,#2c4c7a 0,#18304f 45%,#0c1a30 100%)}
.topbar{position:absolute;top:0;left:0;width:100%;height:87px;background:rgba(8,16,30,.55)}
.brand{position:absolute;left:179px;top:30px;font-size:21px;color:var(--white);font-weight:500}
.brand span{color:var(--blue)}
.nav{position:absolute;top:35px;left:499px;display:flex}
.nav a{color:var(--white);text-decoration:none;font-size:14px;margin-right:29px}
.nav a.active{color:var(--blue)}
.hero-copy{position:absolute;left:181px;top:195px;color:var(--white);width:420px}
.hero-copy h1{font-size:29px;line-height:1.2}
.hero-copy h2{font-size:21px;margin-top:8px}
.hero-copy p{font-size:11.5px;line-height:1.9;margin-top:12px}
.btn-outline{position:absolute;left:184px;top:330px;width:115px;height:36px;border:2px solid var(--white);color:var(--white);font-size:13px;display:flex;align-items:center;justify-content:center;font-family:"Montserrat",sans-serif}
.dots{position:absolute;top:461px;left:562px;display:flex;gap:6px}
.dots i{width:15px;height:15px;border-radius:50%;background:var(--white);border:2px solid rgba(255,255,255,.6)}
.dots i:first-child{background:transparent}

/* services */
.services{top:497px;height:197px}
.service{position:absolute;top:50px;width:270px}
.service svg{position:absolute;left:0;top:0}
.service h3{margin-left:70px;font-size:20px;color:#333}
.service p{margin-left:73px;margin-top:8px;font-size:10.5px;line-height:1.7;color:var(--muted)}
.service a{display:block;margin-left:73px;margin-top:10px;font-size:10.5px;color:var(--blue);text-decoration:none;font-weight:600}

/* why */
.why{top:694px;height:346px;background:var(--grey-bg)}
.why h2{position:absolute;left:181px;top:54px;font-size:25px;color:#222}
.why .copy{position:absolute;left:183px;top:100px;width:420px;font-size:10.5px;line-height:1.75;color:var(--muted)}
.why .copy p+p{margin-top:14px}
.btn-orange{position:absolute;left:184px;top:251px;width:106px;height:33px;background:linear-gradient(var(--orange),var(--orange-dark));color:var(--white);font-size:10px;font-weight:600;display:flex;align-items:center;justify-content:center;border-radius:2px}
.video{position:absolute;left:666px;top:54px;width:349px;height:216px;background:#2a2e34}
.video-still{position:absolute;left:0;top:0;width:349px;height:188px;background:linear-gradient(120deg,#c9d3da 0,#8e9aa4 40%,#3f4750 100%)}
.video svg{position:absolute}

/* projects */
.projects{top:1040px;height:414px}
.projects h2{position:absolute;left:181px;top:43px;font-size:25px}
.card{position:absolute;top:93px;width:196px;text-align:center}
.card .thumb{width:196px;height:131px}
.card h4{font-size:16px;margin-top:14px}
.card p{font-size:9.5px;line-height:1.6;color:var(--muted);margin:6px 10px 0}
.card .btn-blue{display:inline-block;margin-top:12px;width:91px;height:27px;line-height:27px;background:linear-gradient(var(--blue),var(--blue-dark));color:var(--white);font-size:11px;font-weight:600}

/* partners */
.partners{top:1454px;height:99px;border-top:1px solid var(--line);display:flex;justify-content:center;align-items:center;gap:54px}
.partner{display:flex;align-items:center;gap:10px;font-size:19px;color:var(--blue);white-space:nowrap}
.partner i{width:20px;height:20px;background:var(--blue);display:block;flex:none}

/* testimonial */
.testimonial{top:1553px;height:325px;overflow:hidden}
.testimonial .photo{position:absolute;inset:0;background:linear-gradient(90deg,#4a4d52 0,#6f6b66 35%,#5b5a58 60%,#3a3c40 100%)}
.testimonial .shade{position:absolute;inset:0;background:rgba(20,20,25,.35)}
.avatar{position:absolute;left:559px;top:54px;width:82px;height:82px;border-radius:50%;background:#b89b82;border:3px solid rgba(255,255,255,.7)}
.quote{position:absolute;top:145px;left:0;width:1200px;text-align:center;color:var(--white);font-style:italic;font-size:13px;line-height:26px}
.quote b{font-size:28px;line-height:0;font-style:normal;vertical-align:-8px;font-family:Georgia,serif}
.author{position:absolute;top:216px;width:1200px;text-align:center;color:var(--white);font-size:13px;line-height:18px}
.author small{display:block;font-size:10px;line-height:14px;margin-top:2px}

/* footer */
.site-footer{top:1878px;height:255px}
.col{position:absolute;top:38px}
.col h3{font-size:19px;color:var(--blue)}
.col p{font-size:10.5px;line-height:1.75;color:var(--muted)}
.overview p{margin-top:18px;width:240px}
.post{display:flex;gap:12px;margin-top:20px}
.post + .post{margin-top:16px}
.post .thumb{width:67px;height:50px;flex:none}
.post h5{font-size:10.5px;font-weight:600;color:#333}
.post p{width:205px}
.contact li{list-style:none;display:flex;gap:10px;font-size:11px;line-height:1.6;color:#444;margin-top:14px}
.contact li:first-child{margin-top:20px}
.social{display:flex;gap:6px;margin-top:16px}
.social i{width:25px;height:25px;border-radius:50%;background:var(--blue);display:block}
.bottom-bar{position:absolute;top:2133px;left:0;width:1200px;height:54px;background:var(--bar);text-align:center;line-height:54px;font-size:10.5px;color:var(--muted)}
.bottom-bar .code{position:absolute;right:30px;top:6px;font-size:10px;line-height:54px}
</style>
</head>
<body>

<header class="hero">
  <div class="hero-visual" role="img" aria-label="Business person touching a glowing cloud network of connected device icons"></div>
  <div class="topbar"></div>
  <div class="brand"><span>Marrowind</span> IT Consultancy</div>
  <nav class="nav">
    <a class="active" href="#">Home</a><a href="#">About Us</a><a href="#">Services</a><a href="#">Projects</a><a href="#">Testimonials</a><a href="#">Contact</a>
  </nav>
  <div class="hero-copy">
    <h1>Class aptent taciti sociosqu</h1>
    <h2>Litora torquent per conubia nostra</h2>
    <p>Donec dictum lectus non odio Cras a ante vitae enim iaculis aliquam<br>Mauris nunc quam venenatis nec euismod sit amet</p>
  </div>
  <a class="btn-outline">Learn More</a>
  <div class="dots"><i></i><i></i><i></i><i></i></div>
</header>

<section class="services">
  <div class="service" style="left:175px">
    <svg width="62" height="62" viewBox="0 0 62 62"><circle cx="22" cy="22" r="9" fill="#1a6fb8"/><path d="M6 56c0-12 7-20 16-20s16 8 16 20z" fill="#2f8fd6"/><path d="M19 36l3 8 3-8z" fill="#fff"/><rect x="32" y="2" width="22" height="15" rx="7" fill="none" stroke="#2f8fd6" stroke-width="2"/><circle cx="38" cy="10" r="1.5" fill="#2f8fd6"/><circle cx="43" cy="10" r="1.5" fill="#2f8fd6"/><circle cx="48" cy="10" r="1.5" fill="#2f8fd6"/></svg>
    <h3>Consultancy</h3>
    <p>Curabitur vel mi sit amet magna males uada ultrices Ut nisi erat fermentum vel congue massa libero interdum</p>
    <a>Read More</a>
  </div>
  <div class="service" style="left:461px">
    <svg width="62" height="62" viewBox="0 0 62 62"><path d="M22 18a8 8 0 0 1 15-4 7 7 0 0 1 11 6 6 6 0 0 1-2 12H24a7 7 0 0 1-2-14z" fill="#2f8fd6"/><path d="M4 32h10l8 6h14a3 3 0 0 1 0 6H22M14 48l10 4h18l14-12" fill="none" stroke="#1a6fb8" stroke-width="4" stroke-linecap="round"/><rect x="2" y="30" width="10" height="20" fill="#1a6fb8"/></svg>
    <h3>IT Security</h3>
    <p>Curabitur vel mi sit amet magna males uada ultrices Ut nisi erat fermentum vel congue massa libero interdum</p>
    <a>Read More</a>
  </div>
  <div class="service" style="left:746px">
    <svg width="62" height="62" viewBox="0 0 62 62"><path d="M14 34a9 9 0 0 1 2-18 13 13 0 0 1 25-2 10 10 0 0 1 6 20" fill="none" stroke="#2f8fd6" stroke-width="2.5"/><rect x="22" y="34" width="16" height="14" rx="2" fill="none" stroke="#1a6fb8" stroke-width="2.5"/><path d="M25 34v-4a5 5 0 0 1 10 0v4" fill="none" stroke="#1a6fb8" stroke-width="2.5"/><circle cx="30" cy="41" r="2" fill="#1a6fb8"/></svg>
    <h3>Cloud Services</h3>
    <p>Curabitur vel mi sit amet magna males uada ultrices Ut nisi erat fermentum vel congue massa libero interdum</p>
    <a>Read More</a>
  </div>
</section>

<section class="why">
  <h2>Why Choose Us</h2>
  <div class="copy">
    <p>aliquam Curabitur iaculis tempus eros Curabitur vel mi sit amet magna malesuada ultrices Ut nisi erat fermentum vel congue id euismod in elit Fusce ultricies orci ac feugiat suscipit leo massa sodales velit et scelerisque</p>
    <p>mi tortor at ipsum cligula augue bibendum accumsan vestibulum ut commodo a mi Morbi ornare gravida elit Integer congue augue et malesuada iaculis ipsum dui aliquet felis at cursus magna nisl nec elit Praesent elementum elit at tellus nec ultricies sit amet porttitor mattis enim In massa libero interdum</p>
  </div>
  <a class="btn-orange">READ MORE</a>
  <div class="video">
    <div class="video-still" role="img" aria-label="Business team gathered around a laptop in a bright office"></div>
    <svg style="left:150px;top:70px" width="52" height="52" viewBox="0 0 52 52"><circle cx="26" cy="26" r="24" fill="none" stroke="#fff" stroke-width="3"/><path d="M21 15l15 11-15 11z" fill="#fff"/></svg>
    <svg style="left:0;top:188px" width="349" height="28" viewBox="0 0 349 28"><path d="M8 9l8 5-8 5z" fill="#fff"/><rect x="26" y="12" width="262" height="4" rx="2" fill="#ddd"/><rect x="26" y="12" width="95" height="4" rx="2" fill="#2f8fd6"/><path d="M322 11h3l4-3v12l-4-3h-3z" fill="#fff"/><path d="M332 10a5 5 0 0 1 0 8" stroke="#fff" fill="none"/></svg>
  </div>
</section>

<section class="projects">
  <h2>Latest Projects</h2>
  <div class="card" style="left:183px">
    <div class="thumb" role="img" aria-label="Hands holding a glowing cloud infrastructure graphic" style="background:linear-gradient(160deg,#0b1a33,#1d5aa8 60%,#0a1428)"></div>
    <h4>Project Tittle</h4><p>Curabitur vel mi sit amet magna malesuada ultrices Ut nisi erat ferme ntum vel congue id euismod</p><a class="btn-blue">Read More</a>
  </div>
  <div class="card" style="left:396px">
    <div class="thumb" role="img" aria-label="Businessman in a suit with a cloud sketch" style="background:linear-gradient(160deg,#eef4f9,#a9c6e2 55%,#3f6b9c)"></div>
    <h4>Project Tittle</h4><p>Curabitur vel mi sit amet magna malesuada ultrices Ut nisi erat ferme ntum vel congue id euismod</p><a class="btn-blue">Read More</a>
  </div>
  <div class="card" style="left:609px">
    <div class="thumb" role="img" aria-label="Two colleagues reviewing work at a laptop" style="background:linear-gradient(160deg,#e8ecef,#b9c3cb 50%,#6b7680)"></div>
    <h4>Project Tittle</h4><p>Curabitur vel mi sit amet magna malesuada ultrices Ut nisi erat ferme ntum vel congue id euismod</p><a class="btn-blue">Read More</a>
  </div>
  <div class="card" style="left:822px">
    <div class="thumb" role="img" aria-label="Hand holding a cloud icon in a server room" style="background:linear-gradient(160deg,#1c2f44,#3b6c8f 55%,#0f1c2a)"></div>
    <h4>Project Tittle</h4><p>Curabitur vel mi sit amet magna malesuada ultrices Ut nisi erat ferme ntum vel congue id euismod</p><a class="btn-blue">Read More</a>
  </div>
</section>

<section class="partners">
  <div class="partner"><i></i>QNT</div>
  <div class="partner"><i></i>Vantrel Skyline</div>
  <div class="partner"><i></i>Horvik Vapor Platform</div>
  <div class="partner"><i></i>Lumaro Cloud</div>
</section>

<section class="testimonial">
  <div class="photo" role="img" aria-label="Smiling professional in an office with shelves behind"></div>
  <div class="shade"></div>
  <div class="avatar" role="img" aria-label="Client portrait"></div>
  <p class="quote"><b>“</b> Curabitur vel mi sit amet magna malesuada ultrices Ut nisi erat fermentum vel congue id euismod in elit Fusce <b>”</b><br>ultricies orci ac feugiat suscipit leo massa sodales velit et scelerisque mi tortor at ipsum</p>
  <p class="author">By Author Name<small>City Location</small></p>
</section>

<footer class="site-footer">
  <div class="col overview" style="left:182px">
    <h3>Company Overview</h3>
    <p>Curabitur vel mi sit amet magna malesuada ultrices Ut nisi erat fermentum vel congue id euismod in elit Fusce ultricies orci ac feugiat suscipit leo massa sodales velit et scelerisque mi tortor at ipsum cligula augue bibendum accumsan vestibulum</p>
  </div>
  <div class="col blogs" style="left:472px">
    <h3>Latest Blogs</h3>
    <div class="post"><div class="thumb" role="img" aria-label="Blue technology scene" style="background:linear-gradient(#0d2346,#2d6fc0)"></div><div><h5>Curabitur vel mi sit amet</h5><p>magna malesuada ultrices Ut nisi erat fermentum vel congue id</p></div></div>
    <div class="post"><div class="thumb" role="img" aria-label="Sketch of cloud ideas" style="background:linear-gradient(#f1f1f1,#c9c9c9)"></div><div><h5>Curabitur vel mi sit amet</h5><p>magna malesuada ultrices Ut nisi erat fermentum vel congue id</p></div></div>
  </div>
  <div class="col contact" style="left:802px">
    <h3>Find Us</h3>
    <ul>
      <li><svg width="14" height="18" viewBox="0 0 14 18"><path d="M7 0a7 7 0 0 1 7 7c0 5-7 11-7 11S0 12 0 7a7 7 0 0 1 7-7z" fill="#2f8fd6"/><circle cx="7" cy="7" r="2.5" fill="#fff"/></svg><span>412 Harbour Crest Road Suite B20<br>Northgate, QLD 4013</span></li>
      <li><svg width="14" height="14" viewBox="0 0 14 14"><path d="M3 0l3 3-2 2a8 8 0 0 0 5 5l2-2 3 3-2 3C6 14 0 8 0 2z" fill="#2f8fd6"/></svg><span>+00 1234567890</span></li>
      <li><svg width="15" height="12" viewBox="0 0 15 12"><rect width="15" height="12" rx="1" fill="#2f8fd6"/><path d="M1 1l6.5 5L14 1" stroke="#fff" fill="none"/></svg><span>info@companyname.com</span></li>
    </ul>
    <div class="social" aria-label="Social profiles"><i></i><i></i><i></i><i></i></div>
  </div>
</footer>

<div class="bottom-bar">© 2016 Company Name All right reserved Term of Use<span class="code">X14</span></div>

</body>
</html>
```